Income Tax Business Cards - Updates

Need to update these business cards while keeping all the same wording but just update them and make them look nicer and more modern/ on brand with our brand.

Industry/Entity Type

finance

Contact Information for Business Card

we have multiple locations so will just need to easily be able to change the address and phone numbers

Colors

Designer to choose colors to be used in the design.

```html
<!DOCTYPE html>
<html lang="en">
<head>
<meta charset="UTF-8">
<title>Ledgerline Financial Group – Tax Business Cards</title>
<link href="https://fonts.googleapis.com/css2?family=Montserrat:wght@700;800&family=Lato:wght@400;700&display=swap" rel="stylesheet">
<style>
  :root{
    --bg:#2e2e2e;
    --paper:#ffffff;
    --green:#0f5130;
    --green-text:#1f5a3a;
    --green-tint:#e3efe8;
    --red:#c41f28;
    --charcoal:#3a3a3a;
    --ink:#333333;
    --white:#ffffff;
  }
  *{margin:0;padding:0;box-sizing:border-box}
  html,body{width:1200px;height:1000px;overflow:hidden}
  body{background:var(--bg);position:relative;font-family:"Montserrat",sans-serif}

  .card{position:absolute;left:262px;width:676px;height:386px;background:var(--paper);overflow:hidden}
  .card--front{top:71px}
  .card--back{top:543px}

  .brand{position:absolute;display:flex;align-items:center;gap:10px}
  .brand__mark{width:16px;height:16px;border-radius:50%;background:var(--red);flex:none}
  .brand__name{font-family:"Montserrat",sans-serif;font-weight:700;color:var(--green);font-size:22px;line-height:1.1}
  .brand__name span{display:block;font-size:10px;letter-spacing:3px;margin-top:4px}
  .card--front .brand{left:462px;top:52px}
  .card--back .brand{left:460px;top:50px}

  .corner-ornament{position:absolute}
  .corner-ornament--top{left:0;top:0;width:160px;height:108px;
    background:linear-gradient(135deg,var(--green-tint) 0%,rgba(255,255,255,0) 75%)}
  .corner-ornament--bottom{right:0;bottom:0;width:190px;height:140px;
    background:linear-gradient(315deg,var(--green-tint) 0%,rgba(255,255,255,0) 75%)}

  .tag-file{position:absolute;left:26px;top:120px;width:236px;height:62px;background:var(--charcoal);
    transform:rotate(-3deg);box-shadow:2px 4px 6px rgba(0,0,0,.25);
    color:var(--white);font-weight:800;font-size:34px;display:flex;align-items:center;justify-content:center;padding-top:6px}
  .tag-taxes{position:absolute;left:58px;top:188px;width:363px;height:69px;background:var(--red);
    color:var(--white);font-weight:800;font-size:50px;display:flex;align-items:center;justify-content:center;letter-spacing:-.5px}

  .offer{position:absolute;left:26px;font-weight:800;line-height:1.08;color:var(--green-text)}
  .offer .red{color:var(--red)}
  .card--front .offer{top:276px;font-size:37.5px;padding-bottom:6px;border-bottom:3px solid var(--charcoal)}

  .band{position:absolute;left:0;top:24px;width:438px;height:109px;background:var(--green)}
  .band .offer{color:#ececec;top:20px;left:25px;font-size:35px}
  .edge-stripe{position:absolute;left:661px;top:24px;width:15px;height:109px;background:var(--green)}
  .approved{position:absolute;left:24px;top:141px;color:var(--red);font-weight:800;font-size:20.5px}

  .contact-rail{position:absolute;left:25px;top:208px;width:31px;height:136px;background:var(--red);border-radius:12px;box-shadow:1px 3px 5px rgba(0,0,0,.25)}
  .contact-rail svg{position:absolute;left:7px;width:17px;height:17px;fill:none;stroke:var(--white);stroke-width:1.6}
  .contact-list{position:absolute;left:56px;top:224px;list-style:none}
  .contact-list li{width:277px;height:30px;background:var(--charcoal);margin-bottom:7px;
    font-family:"Lato",sans-serif;font-size:20.5px;color:var(--white);display:flex;align-items:center;padding-left:16px;white-space:nowrap}

  .address-list{position:absolute;right:46px;top:224px;list-style:none}
  .address-list li{height:30px;margin-bottom:7px;display:flex;align-items:center;justify-content:flex-end;gap:12px;
    font-family:"Lato",sans-serif;font-size:21px;color:var(--ink)}
  .address-list svg{width:14px;height:18px;fill:var(--red)}
</style>
</head>
<body>

<section class="card card--front" aria-label="Card front">
  <div class="corner-ornament corner-ornament--top" role="img" aria-label="Decorative thin green arc lines in the top-left corner"></div>
  <div class="brand"><span class="brand__mark"></span><div class="brand__name">Ledgerline<span>FINANCIAL GROUP</span></div></div>
  <div class="tag-file">FILE YOUR</div>
  <div class="tag-taxes">TAXES HERE</div>
  <div class="offer">UP TO <span class="red">$6,000</span><br>SAME DAY <span class="red">ADVANCE</span></div>
  <div class="corner-ornament corner-ornament--bottom" role="img" aria-label="Decorative thin green arc lines in the bottom-right corner"></div>
</section>

<section class="card card--back" aria-label="Card back">
  <div class="band">
    <div class="offer">UP TO <span class="red">$6,000</span><br>SAME DAY ADVANCE</div>
  </div>
  <div class="brand"><span class="brand__mark"></span><div class="brand__name">Ledgerline<span>FINANCIAL GROUP</span></div></div>
  <div class="edge-stripe"></div>
  <p class="approved">ON APPROVED TAX RETURNS!</p>

  <div class="contact-rail">
    <svg viewBox="0 0 24 24" style="top:22px"><path d="M6 3l3 1 1 4-2 2q2 4 6 6l2-2 4 1 1 3-2 3Q5 20 3 5z"/></svg>
    <svg viewBox="0 0 24 24" style="top:60px"><rect x="3" y="6" width="18" height="12"/><path d="M3 6l9 7 9-7"/></svg>
    <svg viewBox="0 0 24 24" style="top:97px"><circle cx="12" cy="12" r="9"/><path d="M3 12h18M12 3q-5 9 0 18M12 3q5 9 0 18"/></svg>
  </div>
  <ul class="contact-list">
    <li>+(555)0100 2468</li>
    <li>www.ledgerline-fg.com</li>
    <li>Mesa@ledgerline-fg.com</li>
  </ul>

  <ul class="address-list">
    <li>Address Line 1 <svg viewBox="0 0 14 18"><path d="M7 0a7 7 0 0 0-7 7c0 5 7 11 7 11s7-6 7-11a7 7 0 0 0-7-7zm0 10a3 3 0 1 1 0-6 3 3 0 0 1 0 6z"/></svg></li>
    <li>Address Line 1 <svg viewBox="0 0 14 18"><path d="M7 0a7 7 0 0 0-7 7c0 5 7 11 7 11s7-6 7-11a7 7 0 0 0-7-7zm0 10a3 3 0 1 1 0-6 3 3 0 0 1 0 6z"/></svg></li>
    <li>Address Line 1 <svg viewBox="0 0 14 18"><path d="M7 0a7 7 0 0 0-7 7c0 5 7 11 7 11s7-6 7-11a7 7 0 0 0-7-7zm0 10a3 3 0 1 1 0-6 3 3 0 0 1 0 6z"/></svg></li>
  </ul>
</section>

</body>
</html>
```